Podiatry clinic requires a modern revamp and editing of existing website.

I would like a fresh new look and updated information for my current business website. An easy to navigate site with prominent address and phone number for call to action. We are a podiatry clinic that focuses on general and sports podiatry.
I would like 4 pages; including Home page, About Us, Services & Contact.
www.brambleridgepodiatry.net

Target Market(s)

Active working professionals.

Industry/Entity Type

Medical

Coding

Coded - Design and coding required

Number of Pages Required

4 page

Font styles to use
Sans Serif

Colors
6b449b

Requirements
Must have
• A modern look with logo and active images; clean and uncluttered. Visible phone number and address for call to action.
• 4 pages - Home, About Us, Services, Contact.
• Home page - update address & service logos.
• About Us - update of personal information.
• Services - Revamp of existing page.
• Contact page to include Google map, email & phone number.
Nice to have
• Ability to add content easily; eg. a blog or adding video onto Home page.
• Link to Facebook page.

```html
<!DOCTYPE html>
<html lang="en">
<head>
<meta charset="utf-8">
<title>Bramble Ridge Podiatry</title>
<link rel="stylesheet" href="https://fonts.googleapis.com/css2?family=Arimo:wght@400;700&family=Open+Sans:wght@400;600&display=swap">
<style>
:root{
  --header-bg:#9b83c0;
  --footer-bg:#5b2b8c;
  --brand:#6b449b;
  --white:#ffffff;
  --heading:#555555;
  --body:#555555;
  --accent:#f5a31e;
  --footer-text:#e9e1f3;
  --partner-grey:#d6d1dc;
}
*{margin:0;padding:0;box-sizing:border-box}
html,body{width:1150px;height:1200px;overflow:hidden}
body{position:relative;background:var(--white);font-family:"Open Sans",Arial,sans-serif;color:var(--body)}

.site-header{position:absolute;left:0;top:0;width:1150px;height:115px;background:var(--header-bg)}
.brand{position:absolute;left:136px;top:40px;display:flex;align-items:center;gap:10px}
.brand-mark{width:20px;height:20px;border-radius:50%;background:var(--brand)}
.brand-name{font-family:"Arimo",Arial,sans-serif;font-weight:700;font-size:19px;color:var(--white)}
.header-phone{position:absolute;right:128px;top:18px;display:flex;align-items:center;gap:5px;font-family:"Arimo",Arial,sans-serif;font-size:20px;color:var(--white)}
.main-nav{position:absolute;right:126px;top:66px;display:flex;gap:0}
.main-nav a{display:block;font-family:"Arimo",Arial,sans-serif;font-size:15px;color:var(--white);text-decoration:none;padding:0 25px 25px;position:relative;letter-spacing:.2px}
.main-nav a:last-child{padding-right:0}
.main-nav a.active::after{content:"";position:absolute;left:16px;right:16px;bottom:0;height:3px;background:var(--white)}

.hero{position:absolute;left:0;top:115px;width:1150px;height:439px;background:linear-gradient(180deg,#b9c79e 0%,#8ea874 30%,#8c9488 58%,#9aa39c 100%)}
.hero-photo{position:absolute;inset:0;background:radial-gradient(ellipse at 70% 45%,rgba(240,240,236,.55) 0%,rgba(240,240,236,0) 30%),linear-gradient(90deg,rgba(255,255,255,.15),rgba(40,70,30,.25))}
.hero-title{position:absolute;left:141px;top:140px;width:560px;font-family:"Arimo",Arial,sans-serif;font-size:35px;line-height:49px;color:var(--white);font-weight:400}
.hero-dots{position:absolute;left:145px;top:247px;display:flex;gap:5px}
.hero-dots span{width:16px;height:16px;border-radius:50%;background:var(--white)}
.hero-dots span.current{background:transparent;border:2px solid var(--white)}

.intro{position:absolute;left:0;top:554px;width:1150px;height:368px;background:linear-gradient(180deg,#ffffff 0%,#f2f2f2 100%)}
.intro-photo{position:absolute;left:680px;top:0;width:380px;height:368px;background:radial-gradient(ellipse at 40% 60%,#f0cdbd 0%,#eec6b4 35%,rgba(245,225,215,.6) 60%,rgba(250,250,250,0) 80%)}
.intro-title{position:absolute;left:128px;top:56px;font-family:"Arimo",Arial,sans-serif;font-weight:400;font-size:32px;color:var(--heading)}
.intro-text{position:absolute;left:129px;top:113px;width:530px;font-size:12.6px;line-height:23.3px;color:var(--body)}
.read-more{position:absolute;left:130px;top:273px;width:114px;height:33px;border:2px solid var(--accent);color:var(--accent);font-family:"Arimo",Arial,sans-serif;font-size:13px;display:flex;align-items:center;justify-content:center;text-decoration:none}

.partners{position:absolute;left:0;top:922px;width:1150px;height:114px;background:var(--white);display:flex;align-items:center;justify-content:center;gap:70px}
.partner-badge{width:170px;height:52px;border-radius:6px;background:var(--partner-grey)}

.site-footer{position:absolute;left:0;top:1036px;width:1150px;height:164px;background:var(--footer-bg);color:var(--footer-text)}
.footer-nav{position:absolute;left:136px;top:42px;display:flex;gap:44px}
.footer-nav a{font-family:"Arimo",Arial,sans-serif;font-size:14.5px;color:var(--white);text-decoration:none}
.copyright{position:absolute;left:136px;top:71px;font-size:12px;color:var(--footer-text)}
.social{position:absolute;left:137px;top:102px;display:flex;gap:8px}
.social span{width:33px;height:33px;border-radius:50%;background:#8d74b0}
.contact-list{position:absolute;left:712px;top:34px;list-style:none}
.contact-list li{display:flex;align-items:center;gap:10px;font-size:13.5px;color:var(--footer-text);height:29px}
.contact-list li.phone{font-size:16.5px}
.contact-list svg{width:16px;height:18px;flex:none}
</style>
</head>
<body>

<header class="site-header">
  <div class="brand">
    <span class="brand-mark"></span>
    <span class="brand-name">Bramble Ridge Podiatry</span>
  </div>
  <div class="header-phone">
    <svg width="16" height="16" viewBox="0 0 24 24"><path fill="#fff" d="M6.6 10.8a15.1 15.1 0 0 0 6.6 6.6l2.2-2.2c.3-.3.7-.4 1-.2 1.1.4 2.3.6 3.6.6.6 0 1 .4 1 1V20c0 .6-.4 1-1 1A17 17 0 0 1 3 4c0-.6.4-1 1-1h3.5c.6 0 1 .4 1 1 0 1.3.2 2.5.6 3.6.1.3 0 .7-.2 1z"/></svg>
    1300 472 908
  </div>
  <nav class="main-nav">
    <a href="#" class="active">HOME</a>
    <a href="#">ABOUT US</a>
    <a href="#">PODIATRY SERVICES</a>
    <a href="#">CONTACT</a>
  </nav>
</header>

<section class="hero">
  <div class="hero-photo" role="img" aria-label="Runner's legs in white sports shoes on a park path with blurred greenery"></div>
  <h1 class="hero-title">Foot Clinic is a Podiatry Clinic in the heart of Melbourn</h1>
  <div class="hero-dots"><span class="current"></span><span></span><span></span><span></span></div>
</section>

<section class="intro">
  <div class="intro-photo" role="img" aria-label="Hand holding a bare foot with a red highlighted sore area on the sole"></div>
  <h2 class="intro-title">Bramble Ridge Podiatry</h2>
  <p class="intro-text">Bramble Ridge Podiatry is a Podiatry clinic in the heart of Melbourne CBD. We are located between Alder &amp;amp; Wren Streets in the Harbourview Business Centre / Linden Hotel Complex. Our podiatrists are fully qualified health professionals who are able to diagnose, treat, manage or help to prevent all medical conditions that affect the feet and lower limb. We provide General Podiatry Treatment and some Specialised Services in relation to various foot conditions, including Sports Injuries</p>
  <a href="#" class="read-more">Read More</a>
</section>

<section class="partners" aria-label="Partners">
  <span class="partner-badge"></span>
  <span class="partner-badge"></span>
  <span class="partner-badge"></span>
  <span class="partner-badge"></span>
</section>

<footer class="site-footer">
  <nav class="footer-nav">
    <a href="#">HOME</a>
    <a href="#">ABOUT US</a>
    <a href="#">PODIATRY SERVICES</a>
    <a href="#">CONTACT</a>
  </nav>
  <p class="copyright">© 2016 Company Name&nbsp; All right reserved&nbsp; Term of Use</p>
  <div class="social"><span></span><span></span><span></span><span></span><span></span></div>
  <ul class="contact-list">
    <li><svg viewBox="0 0 24 24"><path fill="#fff" d="M12 2a7 7 0 0 0-7 7c0 5.2 7 13 7 13s7-7.8 7-13a7 7 0 0 0-7-7zm0 9.5A2.5 2.5 0 1 1 12 6.5a2.5 2.5 0 0 1 0 5z"/></svg>Suite 208 / 155 Harrow Lane Melbourne 3000</li>
    <li><svg viewBox="0 0 24 24"><path fill="#fff" d="M2 5h20v14H2zm2 2v.5l8 5 8-5V7z"/></svg>info@brambleridgepodiatry.net</li>
    <li class="phone"><svg viewBox="0 0 24 24"><path fill="#fff" d="M6.6 10.8a15.1 15.1 0 0 0 6.6 6.6l2.2-2.2c.3-.3.7-.4 1-.2 1.1.4 2.3.6 3.6.6.6 0 1 .4 1 1V20c0 .6-.4 1-1 1A17 17 0 0 1 3 4c0-.6.4-1 1-1h3.5c.6 0 1 .4 1 1 0 1.3.2 2.5.6 3.6.1.3 0 .7-.2 1z"/></svg>1300 472 908</li>
  </ul>
</footer>

</body>
</html>
```